Book cover for book about Climate Change

Looking for a clean, bold, and attractive cover for a mass-market paperback (5.5"x 8.5") about solving the climate change problem. Title is either "Where the Rivers Meet” or A Harbor Made of Glass” (your choice), subtitle is "A practical field guide to mending the weather — so that the young ones after us inherit steady seasons and open skies," author is Lorne Whitcombe. Thinking that it *might* feature an image of Earth (or a portion thereof) and its very thin layer of atmosphere -- but STRONGLY encourage other ideas too!

Requirements
Nice to have
• Keep it positive — NOT scary doom-and-gloom

```html
<!DOCTYPE html>
<html lang="en">
<head>
<meta charset="utf-8">
<title>A Harbor Made of Glass — Lorne Whitcombe</title>
<link rel="stylesheet" href="https://fonts.googleapis.com/css2?family=Old+Standard+TT:wght@400;700&family=Marcellus&family=Noticia+Text:ital@1&display=swap">
<style>
  :root {
    --backdrop: #e2e1e2;
    --paper: #ffffff;
    --ink: #111111;
    --accent: #f08422;
    --sphere-light: #5fa9e0;
    --sphere-mid: #1f72b8;
    --sphere-deep: #0d3f78;
    --shadow: rgba(40, 40, 40, 0.55);
  }
  * { margin: 0; padding: 0; box-sizing: border-box; }
  html, body {
    width: 1200px;
    height: 691px;
    overflow: hidden;
    background: var(--backdrop);
  }
  .cover {
    position: absolute;
    left: 385px;
    top: 0;
    width: 430px;
    height: 691px;
    background: var(--paper);
    box-shadow: 0 2px 10px rgba(0,0,0,0.12);
    text-align: center;
  }
  .cover-title { font-size: inherit; font-weight: inherit; }
  .title-lead {
    position: absolute;
    top: 22px;
    left: 0; right: 0;
    font-family: "Old Standard TT", serif;
    font-weight: 700;
    font-size: 100px;
    line-height: 1;
    color: var(--ink);
  }
  .title-main {
    position: absolute;
    top: 100px;
    left: 0; right: 0;
    font-family: "Old Standard TT", serif;
    font-weight: 700;
    font-size: 92px;
    line-height: 1;
    letter-spacing: -1px;
    color: var(--accent);
  }
  .title-tail {
    position: absolute;
    top: 188px;
    left: 28px; right: 28px;
    display: flex;
    align-items: center;
    gap: 10px;
    font-family: "Old Standard TT", serif;
    font-weight: 400;
    font-size: 36px;
    line-height: 1;
    color: var(--ink);
    white-space: nowrap;
  }
  .title-tail::before,
  .title-tail::after {
    content: "";
    flex: 1;
    height: 2px;
    background: var(--ink);
  }
  .globe {
    position: absolute;
    top: 240px;
    left: 112px;
    width: 206px;
    height: 206px;
    border-radius: 50%;
    background: radial-gradient(circle at 38% 35%, var(--sphere-light) 0%, var(--sphere-mid) 55%, var(--sphere-deep) 100%);
  }
  .globe-shadow {
    position: absolute;
    top: 476px;
    left: 170px;
    width: 90px;
    height: 8px;
    border-radius: 50%;
    background: radial-gradient(ellipse at center, var(--shadow), transparent 70%);
  }
  .rule {
    position: absolute;
    left: 62px;
    width: 306px;
    height: 2px;
    background: linear-gradient(90deg, transparent, var(--ink) 20%, var(--ink) 80%, transparent);
  }
  .rule-top { top: 500px; }
  .rule-bottom { top: 606px; }
  .subtitle {
    position: absolute;
    top: 509px;
    left: 0; right: 0;
    font-family: "Marcellus", serif;
    font-size: 24px;
    line-height: 25px;
    color: var(--accent);
    letter-spacing: 0.5px;
  }
  .subtitle-note {
    position: absolute;
    top: 562px;
    left: 0; right: 0;
    font-family: "Noticia Text", serif;
    font-style: italic;
    font-size: 16px;
    line-height: 19px;
    color: var(--ink);
  }
  .author {
    position: absolute;
    top: 628px;
    left: 0; right: 0;
    font-family: "Marcellus", serif;
    font-size: 37px;
    line-height: 1;
    letter-spacing: 2px;
    color: var(--accent);
    white-space: nowrap;
  }
</style>
</head>
<body>
  <main class="cover">
    <h1 class="cover-title">
      <span class="title-lead">A</span>
      <span class="title-main">HARBOR</span>
      <span class="title-tail">MADE OF GLASS</span>
    </h1>
    <div class="globe" role="img" aria-label="Illustration of planet Earth seen from space"></div>
    <div class="globe-shadow"></div>
    <div class="rule rule-top"></div>
    <p class="subtitle">A PRACTICAL FIELD GUIDE<br>TO MENDING THE WEATHER</p>
    <p class="subtitle-note">– so that the young ones after us inherit<br>steady seasons and open skies</p>
    <div class="rule rule-bottom"></div>
    <p class="author">LORNE WHITCOMBE</p>
  </main>
</body>
</html>
```